Business Cards for a law firm

Business cards for our law firm. Use our silhoette logo and OAK PARTNERS - check our website (www.oakpartners.example)

Contact Information for Business Card

our silhouette logo, OAK PARTNERS, 800-555-0147, Dorian Pemberton, dorian@oakpartners.example

Requirements
Must have
• our silhouette logo, OAK PARTNERS, 800-555-0147, Dorian Pemberton, dorian@oakpartners.example

```html
<!DOCTYPE html>
<html lang="en">
<head>
<meta charset="utf-8">
<title>Oak Partners – Business Cards</title>
<link rel="stylesheet" href="https://fonts.googleapis.com/css2?family=Cinzel:wght@700&family=Arimo:wght@400&display=swap">
<style>
  :root {
    --backdrop: #4b4b4d;
    --paper: #f4f4f2;
    --navy: #1b2d6b;
    --navy-deep: #13224f;
    --ink: #3a3a3c;
    --accent: #d98a1c;
    --divider: #8e8e90;
    --white: #ffffff;
  }
  * { margin: 0; padding: 0; box-sizing: border-box; }
  html, body {
    width: 1200px;
    height: 1108px;
    overflow: hidden;
    background: var(--backdrop);
  }
  .sheet {
    position: relative;
    width: 1200px;
    height: 1108px;
    display: flex;
    flex-direction: column;
    align-items: center;
    justify-content: center;
    gap: 40px;
  }
  .card {
    width: 840px;
    height: 480px;
    position: relative;
    border-bottom: 4px solid var(--accent);
    box-shadow: 0 10px 30px rgba(0,0,0,.35);
  }
  .card--front {
    background: var(--paper);
    display: flex;
    align-items: center;
  }
  .card--back {
    background: radial-gradient(ellipse at 45% 35%, var(--navy-deep) 0%, var(--navy) 70%);
    display: flex;
    align-items: center;
    justify-content: center;
  }
  .brand {
    display: flex;
    align-items: center;
    gap: 14px;
    font-family: "Cinzel", serif;
    font-weight: 700;
    letter-spacing: .08em;
    white-space: nowrap;
  }
  .brand__mark {
    display: block;
    background: currentColor;
  }
  .brand--front {
    color: var(--navy);
    font-size: 24px;
    margin-left: 90px;
    width: 320px;
  }
  .brand--front .brand__mark { width: 30px; height: 30px; }
  .brand--back {
    color: var(--white);
    font-size: 52px;
  }
  .brand--back .brand__mark { width: 62px; height: 62px; }
  .divider {
    width: 1px;
    height: 140px;
    background: var(--divider);
    margin: 0 40px 0 30px;
  }
  .person__name {
    font-family: "Cinzel", serif;
    font-weight: 700;
    font-size: 27px;
    letter-spacing: .04em;
    color: var(--navy);
    margin-bottom: 18px;
    white-space: nowrap;
  }
  .contact {
    list-style: none;
    font-family: "Arimo", sans-serif;
    font-size: 17px;
    color: var(--ink);
  }
  .contact__item {
    display: flex;
    align-items: center;
    gap: 12px;
    line-height: 26px;
  }
  .contact__icon { width: 14px; height: 14px; flex: none; }
</style>
</head>
<body>
<main class="sheet">
  <section class="card card--front" aria-label="Business card front">
    <div class="brand brand--front">
      <span class="brand__mark"></span>
      <span class="brand__name">OAK PARTNERS</span>
    </div>
    <div class="divider"></div>
    <div class="person">
      <h1 class="person__name">Dorian Pemberton</h1>
      <ul class="contact">
        <li class="contact__item">
          <svg class="contact__icon" viewBox="0 0 16 16"><path fill="#d98a1c" d="M3.5 1 6 1.5 7 5 5.3 6.3c.8 1.8 2.3 3.3 4.2 4.2L10.8 9l3.4 1-0.2 2.6C13.8 14 12.5 15 11 15 5.8 14.3 1.7 10.2 1 5 1 3.5 2 1.3 3.5 1Z"/></svg>
          <span>800-555-0147</span>
        </li>
        <li class="contact__item">
          <svg class="contact__icon" viewBox="0 0 16 16"><rect x="1" y="3" width="14" height="10" fill="#d98a1c"/><path d="M1.5 3.5 8 9l6.5-5.5" fill="none" stroke="#f4f4f2" stroke-width="1.3"/></svg>
          <span>dorian@oakpartners.example</span>
        </li>
        <li class="contact__item">
          <svg class="contact__icon" viewBox="0 0 16 16"><circle cx="8" cy="8" r="7" fill="#d98a1c"/><path d="M1 8h14M8 1c-3 3.5-3 10.5 0 14M8 1c3 3.5 3 10.5 0 14" fill="none" stroke="#f4f4f2" stroke-width="1"/></svg>
          <span>www.oakpartners.example</span>
        </li>
      </ul>
    </div>
  </section>

  <section class="card card--back" aria-label="Business card back">
    <div class="brand brand--back">
      <span class="brand__mark"></span>
      <span class="brand__name">OAK PARTNERS</span>
    </div>
  </section>
</main>
</body>
</html>
```